Modern Verdell Tree Care Website

I need a website for a full service Tree Care company. The company provides tree pruning, tree removal, tree preservation, emergency services, stump grinding, and emergency tree services.

Target Market(s)

Customers that need tree services

Industry/Entity Type

Landscaping, Tree Services

Coding

Coded - Design and coding required

Number of Pages Required

5+ page

Font styles to use
Sans Serif

Requirements
Must have
• Good clean design that showcases the services the company provides.
Nice to have
• Services page; contact form, blog, home page, about page

```html
<!DOCTYPE html>
<html lang="en">
<head>
<meta charset="utf-8">
<title>Verdell Tree Care</title>
<link href="https://fonts.googleapis.com/css2?family=Red+Hat+Display:wght@400;500;600;700;800&display=swap" rel="stylesheet">
<style>
:root{
  --lime:#8dc63f;
  --orange:#f7a325;
  --tan:#c8955e;
  --dark:#1d2e0c;
  --forest:#2f5414;
  --ink:#3b4a57;
  --muted:#8a929a;
  --paper:#f5f7fb;
  --white:#ffffff;
}
*{box-sizing:border-box;margin:0;padding:0}
html,body{width:1200px;height:3382px;overflow:hidden}
body{background:var(--lime);font-family:"Red Hat Display",sans-serif;color:var(--ink);position:relative}
.page{position:absolute;left:88px;top:88px;width:1024px;height:3205px;background:var(--paper);overflow:hidden}
.abs{position:absolute}
.btn{position:absolute;display:flex;align-items:center;justify-content:center;gap:7px;background:var(--orange);color:#fff;font-weight:700;font-size:11px;border-radius:3px}
.btn .sq{width:10px;height:10px;background:#fff;border-radius:2px}
.brand{position:absolute;display:flex;align-items:center;gap:8px;font-weight:800;font-size:22px;color:var(--orange);letter-spacing:.5px}
.brand .mark{width:22px;height:22px;background:var(--lime)}
.nav{position:absolute;top:20px;left:353px;display:flex;gap:28px;font-size:11px;color:#555}
.nav .on{color:var(--lime);font-weight:600}
.hero{position:absolute;left:0;top:0;width:1024px;height:538px;background:linear-gradient(180deg,#cfe2c4 0%,#4f7a2e 22%,#3d6a22 55%,#4f8a2a 85%,#5c9a32 100%)}
.hero h1{position:absolute;top:200px;width:100%;text-align:center;color:#fff;font-size:27px;font-weight:800}
.hero p{position:absolute;top:242px;width:100%;text-align:center;color:#f1f1f1;font-size:12px}
.sec-mark{position:absolute;width:18px;height:16px;background:var(--lime);left:503px}
.sec-title{position:absolute;width:100%;text-align:center;font-size:22px;font-weight:700;color:#4a5866}
.card-img{position:absolute;border-radius:6px}
.card-txt{position:absolute;background:#eef0f3;border-radius:6px;padding:14px 16px}
.card-txt h3{font-size:16px;font-weight:700;color:#4a5866}
.card-txt p{font-size:8px;color:var(--muted);width:140px;margin-top:6px;line-height:1.4}
.card-txt .arr{position:absolute;right:16px;top:17px;width:42px;height:42px;border:1px solid #c9cdd3;border-radius:4px;background:#fff;display:flex;align-items:center;justify-content:center}
.card-txt.hot{background:var(--tan)}
.card-txt.hot h3,.card-txt.hot p{color:#fff}
.about{position:absolute;left:0;top:1385px;width:1024px;height:500px;background:radial-gradient(circle at 40% 50%,#2a4314,#111c07)}
.about h2{position:absolute;left:150px;top:115px;color:#fff;font-size:20px;font-weight:800}
.about p{position:absolute;left:150px;width:385px;color:#e4e8df;font-size:11px;line-height:1.5}
.why-card{position:absolute;width:168px;height:109px;background:#fff;border-radius:6px;display:flex;flex-direction:column;align-items:center;justify-content:center;gap:10px;font-size:12px;color:#4a5866;text-align:center;line-height:1.35}
.why-card .ic{width:20px;height:20px;border:2px solid var(--lime);border-radius:4px}
.testi{position:absolute;width:230px;height:131px;background:#fff;border:1px solid #eceef1;border-radius:6px;padding:20px 18px}
.testi .av{position:absolute;left:18px;top:20px;width:40px;height:40px;border-radius:50%}
.testi .nm{position:absolute;left:72px;top:24px;font-size:9px;color:#555}
.testi .st{position:absolute;left:72px;top:37px;font-size:10px;color:var(--orange);letter-spacing:1px}
.testi .q{position:absolute;right:18px;top:18px;color:var(--orange);font-weight:800;font-size:14px}
.testi p{position:absolute;left:18px;top:76px;width:195px;font-size:8px;color:var(--muted);line-height:1.5;font-style:italic}
.footer{position:absolute;left:0;top:2883px;width:1024px;height:322px;background:var(--forest)}
.cta{position:absolute;left:150px;top:2782px;width:724px;height:192px;background:var(--lime);border-radius:6px;text-align:center;color:#fff}
.fcol{position:absolute;top:261px;color:#fff}
.fcol h4{font-size:12px;font-weight:600;margin-bottom:10px}
.fcol li{list-style:none;font-size:9px;line-height:18px;color:#e8eedd}
</style>
</head>
<body>
<div class="page">
  <div class="hero" role="img" aria-label="Large spreading tree in a green park with a person walking"></div>
  <div class="brand" style="left:150px;top:14px"><span class="mark"></span>Verdell</div>
  <nav class="nav"><span class="on">Home</span><span>About Us</span><span>Services ⌄</span><span>Blog</span><span>Contact Us</span></nav>
  <div class="btn" style="left:734px;top:11px;width:140px;height:31px;font-size:11px;font-weight:600">
    <svg width="11" height="11" viewBox="0 0 24 24"><path fill="#fff" d="M6.6 10.8a15 15 0 0 0 6.6 6.6l2.2-2.2a1 1 0 0 1 1-.2 11 11 0 0 0 3.6.6 1 1 0 0 1 1 1V20a1 1 0 0 1-1 1A17 17 0 0 1 3 4a1 1 0 0 1 1-1h3.5a1 1 0 0 1 1 1c0 1.2.2 2.4.6 3.6a1 1 0 0 1-.3 1z"/></svg>337 555-0148</div>
  <div class="hero" style="background:none">
    <h1>YOUR TRUSTED TREE CARE EXPERTS</h1>
    <p>Comprehensive tree care services for a healthy and beautiful landscape.</p>
  </div>
  <div class="btn" style="left:438px;top:284px;width:148px;height:31px"><span class="sq"></span>Get a Free Quote</div>

  <!-- Services -->
  <div class="sec-mark" style="top:617px"></div>
  <div class="sec-title" style="top:638px">OUR SERVICES</div>
  <div class="abs" style="top:678px;width:100%;text-align:center;font-size:12px;color:var(--muted)">Serving Lafayette and surrounding areas</div>

  <div class="card-img" style="left:150px;top:729px;width:229px;height:160px;background:linear-gradient(135deg,#3d6b1f,#7ea43c)" role="img" aria-label="Gloved hands pruning a branch with shears"></div>
  <div class="card-txt" style="left:150px;top:899px;width:229px;height:79px"><h3>Tree Pruning</h3><p>Enhance the health and appearance of your trees with precise pruning.</p><span class="arr"><svg width="14" height="14" viewBox="0 0 14 14"><path d="M3 11L11 3M5 3h6v6" stroke="#f7a325" stroke-width="1.6" fill="none"/></svg></span></div>

  <div class="card-img" style="left:396px;top:712px;width:231px;height:160px;background:linear-gradient(135deg,#4a5a2c,#a88a5a)" role="img" aria-label="Chainsaw cutting through a log"></div>
  <div class="card-txt hot" style="left:396px;top:881px;width:231px;height:81px"><h3>Tree Removal</h3><p>Safe and efficient tree removal to protect your property.</p><span class="arr" style="border:none"><svg width="14" height="14" viewBox="0 0 14 14"><path d="M3 11L11 3M5 3h6v6" stroke="#f7a325" stroke-width="1.6" fill="none"/></svg></span></div>

  <div class="card-img" style="left:643px;top:729px;width:231px;height:160px;background:linear-gradient(135deg,#7a8b4a,#c6a46a)" role="img" aria-label="Hands planting a young tree sapling"></div>
  <div class="card-txt" style="left:643px;top:899px;width:231px;height:79px"><h3>Tree Preservation</h3><p>Preserve the life and beauty of your trees with our expert care.</p><span class="arr"><svg width="14" height="14" viewBox="0 0 14 14"><path d="M3 11L11 3M5 3h6v6" stroke="#f7a325" stroke-width="1.6" fill="none"/></svg></span></div>

  <div class="card-img" style="left:150px;top:996px;width:229px;height:161px;background:linear-gradient(135deg,#4a5e2a,#c8a23a)" role="img" aria-label="Crew working in a bucket lift among branches"></div>
  <div class="card-txt" style="left:150px;top:1167px;width:229px;height:80px"><h3>Emergency Servi...</h3><p>Quick response for all your tree-related emergencies.</p><span class="arr"><svg width="14" height="14" viewBox="0 0 14 14"><path d="M3 11L11 3M5 3h6v6" stroke="#f7a325" stroke-width="1.6" fill="none"/></svg></span></div>

  <div class="card-img" style="left:396px;top:979px;width:231px;height:161px;background:linear-gradient(135deg,#3f3a2c,#8a6a44)" role="img" aria-label="Tree stump among autumn leaves"></div>
  <div class="card-txt" style="left:396px;top:1149px;width:231px;height:81px"><h3>Stump Grinding</h3><p>Effective stump removal for a clean and tidy landscape.</p><span class="arr"><svg width="14" height="14" viewBox="0 0 14 14"><path d="M3 11L11 3M5 3h6v6" stroke="#f7a325" stroke-width="1.6" fill="none"/></svg></span></div>

  <div class="card-img" style="left:643px;top:996px;width:231px;height:161px;background:linear-gradient(135deg,#4f5f3a,#8c9a78)" role="img" aria-label="Fallen tree across a park path after a storm"></div>
  <div class="card-txt" style="left:643px;top:1167px;width:231px;height:80px"><h3>Strom Damage Cl...</h3><p>Enhance the health and appearance of your trees with precise pruning.</p><span class="arr"><svg width="14" height="14" viewBox="0 0 14 14"><path d="M3 11L11 3M5 3h6v6" stroke="#f7a325" stroke-width="1.6" fill="none"/></svg></span></div>

  <div class="btn" style="left:402px;top:1275px;width:220px;height:30px"><span class="sq"></span>Learn More About Our Services</div>

  <!-- About -->
  <div class="about">
    <div class="abs" style="left:150px;top:92px;width:18px;height:16px;background:var(--lime)"></div>
    <h2>ABOUT VERDELL TREE CARE</h2>
    <p style="top:160px">At Verdell Tree Care, we are more than just a tree service company, we are stewards of our beautiful trees. With a passion deeply rooted in arboriculture, we embark on a mission to promote the health, beauty, and safety of your trees and landscapes.</p>
    <p style="top:235px">Whether it's expert tree trimming to enhance aesthetics, meticulous tree removal to mitigate hazards, or comprehensive tree health assessment to ensure safety, we approach each task with unwavering dedication and attention to details.</p>
    <div class="abs" style="left:150px;top:314px;width:148px;height:31px;border:1px solid var(--orange);border-radius:3px;display:flex;align-items:center;justify-content:center;gap:7px;color:var(--orange);font-weight:700;font-size:11px"><span style="width:10px;height:10px;background:var(--orange);border-radius:2px"></span>Get a Free Quote</div>
    <div class="abs" style="left:575px;top:79px;width:297px;height:343px;border-radius:6px;background:linear-gradient(160deg,#6aa03a,#3b6e1f 60%,#8fa870)" role="img" aria-label="Arborist in cap and overalls trimming a pine tree"></div>
  </div>

  <!-- Why -->
  <div class="sec-mark" style="top:1973px"></div>
  <div class="sec-title" style="top:1994px">WHY CHOOSE US?</div>
  <div class="why-card" style="left:150px;top:2031px"><span class="ic"></span>Licensed and Insured</div>
  <div class="why-card" style="left:335px;top:2031px"><span class="ic" style="border-radius:50%"></span>24-Hours Emergency<br>Services</div>
  <div class="why-card" style="left:520px;top:2031px"><span class="ic" style="border-radius:50% 50% 50% 0"></span>Locally Owned &amp;<br>Operated</div>
  <div class="why-card" style="left:706px;top:2031px"><span class="ic"></span>Professional Work</div>
  <div class="why-card" style="left:243px;top:2158px"><span class="ic"></span>Safety is Our No.1<br>Priorty</div>
  <div class="why-card" style="left:428px;top:2158px"><span class="ic"></span>Free Estimates</div>
  <div class="why-card" style="left:613px;top:2158px"><span class="ic"></span>Licensed Arborist in<br>Staff</div>
  <div class="btn" style="left:437px;top:2294px;width:148px;height:31px"><span class="sq"></span>Get a Free Quote</div>

  <!-- Testimonials -->
  <div class="abs" style="left:0;top:2402px;width:1024px;height:480px;background:#fff"></div>
  <div class="sec-mark" style="top:2491px"></div>
  <div class="sec-title" style="top:2512px">WHAT OUR CUSTOMERS SAY</div>
  <div class="testi" style="left:150px;top:2551px"><span class="av" style="background:#8ec5e0" role="img" aria-label="Customer avatar"></span><span class="nm">Jane D.</span><span class="st">★★★★★</span><span class="q">❞</span><p>Modern Verdell Tree Care transformed our yard. Their team was professional and efficient. Highly recommend!</p></div>
  <div class="testi" style="left:397px;top:2551px"><span class="av" style="background:#f2c04a" role="img" aria-label="Customer avatar"></span><span class="nm">Sarah K.</span><span class="st">★★★★★</span><span class="q">❞</span><p style="font-style:normal">Excellent service and great results! Our trees have never looked better.</p></div>
  <div class="testi" style="left:643px;top:2551px"><span class="av" style="background:#c25aa0" role="img" aria-label="Customer avatar"></span><span class="nm">John S.</span><span class="st">★★★★★</span><span class="q">❞</span><p style="font-style:normal">Quick response to an emergency tree removal. Lifesavers!</p></div>
  <div class="abs" style="left:485px;top:2698px;width:20px;height:3px;background:var(--tan);border-radius:2px"></div>
  <div class="abs" style="left:509px;top:2698px;width:10px;height:3px;background:var(--tan);border-radius:2px"></div>
  <div class="abs" style="left:523px;top:2698px;width:10px;height:3px;background:var(--tan);border-radius:2px"></div>

  <!-- Footer -->
  <div class="footer">
    <div class="brand" style="left:150px;top:238px;color:#fff"><span class="mark"></span>Verdell</div>
    <p class="abs" style="left:150px;top:280px;width:160px;font-size:9px;line-height:1.4;color:#e8eedd">At Verdell Tree Care, we are more than just a tree service company, we are stewards of our beautiful trees.</p>
    <div class="fcol" style="left:349px"><h4>Quick Links</h4><ul><li>About Us</li><li>Services</li><li>Blog</li><li>Contact Us</li></ul></div>
    <div class="fcol" style="left:446px"><h4>Contact Info</h4><ul><li>☏ 555-123-4567</li><li>✉ hello@verdelltreecare.com</li><li>⌖ 123 Tree Lane, Arbor City, ST 12345</li></ul></div>
    <div class="fcol" style="left:643px"><h4>Newsletter Signup</h4><ul><li>Stay Updated with Our Latest Tips and News</li></ul></div>
    <div class="abs" style="left:643px;top:300px;width:141px;height:31px;background:#f3f3f3;border-radius:3px;font-size:9px;color:#999;padding:10px 11px">Enter your email</div>
    <div class="btn" style="left:803px;top:300px;width:71px;height:31px;font-size:10px">Subscribe</div>
    <div class="abs" style="left:150px;top:378px;width:724px;height:1px;background:rgba(255,255,255,.25)"></div>
    <div class="abs" style="left:0;top:390px;width:1024px;text-align:center;font-size:8px;color:#e8eedd">© Copyright 2024, Inc. All Rights Reserved.</div>
  </div>
  <div class="cta">
    <div class="abs" style="left:353px;top:40px;width:18px;height:16px;background:#fff"></div>
    <div class="abs" style="top:58px;width:100%;font-size:20px;font-weight:800">READY TO IMPROVE YOUR LANDSCAPE?</div>
    <div class="abs" style="top:93px;width:100%;font-size:11px;color:#f3f8ea">Contact us today for a free quote or to schedule a consultation with our tree care experts.</div>
    <div class="btn" style="left:291px;top:128px;width:142px;height:30px"><span class="sq"></span>Contact Us Now</div>
  </div>
</div>
</body>
</html>
```